Wellness, Meaning, and the Inner Journey Research Program Website

Overview: This website will serve a new research program (Wellness, Meaning, and the Inner Journey) at the Harrowgate University School of Medicine. I want a clean, intuitive design that has a navigation bar, but uses icons/graphic buttons to link to the main pages. In an attached Word document, I have provided a basic information architecture for the site, understanding that this project would just generate graphics and code for the 3 pages. I highlighted the 3 pages I'd like designed.
Target market: People who want to participate in our research, or contribute grant funding to specific projects.
Number of page: The design project focuses on 3 pages, but the site must accommodate 6 pages with top-level links. See attached Word doc.
Logo and website header: Please integrate our logo in the header. I've uploaded it as a png file--both with the name of the website and with just the logo image. I imaging the logo would look great in a banner set against an image of a mountain. The two main design themes I want to see included are nature and healthcare.
Text content: I have not yet provided text. Use some dummy text.
Technical Specifications:
- Build using WordPress. We will host this site ourselves on NetHarbor using WordPress.
- The design package must be coded.
- The template must be responsive to different platforms (e.g., computer, mobile phone, iPad).
Thank you! I look forward to seeing your designs.
- Ned

```html
<!DOCTYPE html>
<html lang="en">
<head>
<meta charset="utf-8">
<title>Wellness, Meaning, and the Inner Journey – The Research Program</title>
<link href="https://fonts.googleapis.com/css2?family=Poppins:wght@400;500;600&family=Fredoka:wght@500;600&display=swap" rel="stylesheet">
<style>
:root{
  --blue:#1b5f9f;
  --blue-dark:#174f86;
  --green:#5ba53b;
  --teal:#10a48b;
  --teal-dark:#0c8d77;
  --mint:#f0f5ef;
  --ink:#2a2a2a;
  --muted:#666;
  --white:#fff;
}
*{margin:0;padding:0;box-sizing:border-box}
html,body{width:1200px;height:3602px;overflow:hidden}
body{position:relative;font-family:"Poppins",sans-serif;color:var(--ink);background:var(--white)}
.abs{position:absolute}
.center{text-align:center;left:0;width:1200px}

/* nav */
.topnav{position:absolute;top:0;left:0;width:1200px;height:56px;background:rgba(120,140,170,.35);z-index:3;border-bottom:1px solid rgba(255,255,255,.3)}
.nav-item{position:absolute;top:8px;width:120px;margin-left:-60px;text-align:center;color:#eef3fa;font-size:13px}
.nav-item svg{display:block;margin:0 auto 4px;width:18px;height:18px}
.nav-item.active{color:var(--blue)}
.nav-item.active::after{content:"";display:block;width:38px;height:2px;background:var(--blue);margin:4px auto 0}

/* hero */
.hero{position:absolute;top:0;left:0;width:1200px;height:620px}
.hero-photo{position:absolute;inset:0;background:linear-gradient(180deg,#9fb5cc 0%,#dfe2e4 28%,#f3e6d7 36%,#b9c6d4 55%,#6a7f97 75%,#5c6f86 100%)}
.hero-logo{position:absolute;left:568px;top:100px;width:64px;height:64px;border-radius:50%;background:var(--green)}
.hero-title{top:212px;font-family:"Fredoka",sans-serif;font-weight:600;font-size:37px;color:var(--blue)}
.hero-sub{top:258px;font-family:"Fredoka",sans-serif;font-weight:600;font-size:30px;color:var(--green)}
.hero-text{top:304px;font-size:23px;line-height:37px;color:#1f1f1f}
.btn{position:absolute;height:39px;width:140px;border-radius:3px;background:linear-gradient(90deg,var(--blue),var(--green));color:#fff;font-size:13px;display:flex;align-items:center;justify-content:center}

/* sections */
.band-mint{position:absolute;left:0;width:1200px;background:var(--mint)}
.sec-title{font-family:"Fredoka",sans-serif;font-weight:600;font-size:36px;color:var(--blue)}
.sec-title span{color:var(--green)}
.ornament{display:block;margin:4px auto 0}
.lead{font-size:14.5px;line-height:23px;color:#333}

/* vision cards */
.v-card{position:absolute;top:870px;width:273px;height:372px;background:#fff;border-radius:8px;box-shadow:0 3px 10px rgba(0,0,0,.12);text-align:center}
.v-photo{position:absolute;left:7px;top:7px;width:259px;height:179px;border-radius:4px}
.v-icon{position:absolute;left:100px;top:144px;width:74px;height:74px;border-radius:50%;border:4px solid #fff;background:linear-gradient(135deg,var(--blue),var(--green));display:flex;align-items:center;justify-content:center}
.v-card h3{position:absolute;top:237px;width:100%;font-size:15px;font-weight:600}
.v-card p{position:absolute;top:268px;left:14px;right:14px;font-size:14px;line-height:24px;color:#333}

/* pillars */
.pillar h4{font-size:19px;font-weight:500;color:#222}
.pillar p{font-size:11.5px;line-height:19px;color:#666;margin-top:4px}
.pillar .more{display:block;color:var(--green);font-size:15px;margin-top:4px}

/* projects */
.p-card{position:absolute;top:2256px;width:199px;height:261px;border-radius:8px;overflow:visible}
.p-photo{position:absolute;inset:0;border-radius:8px}
.p-card h5{position:absolute;left:0;width:100%;text-align:center;color:#fff;font-size:16px;font-weight:600}
.p-card small{position:absolute;left:0;width:100%;text-align:center;color:#fff;font-size:12px}
.plus{position:absolute;width:30px;height:30px;border-radius:50%;background:#fff;box-shadow:0 2px 5px rgba(0,0,0,.25);left:84px;display:flex;align-items:center;justify-content:center;font-size:20px;font-weight:600;color:#222}
.arrow{position:absolute;top:2368px;width:36px;height:36px;border-radius:50%;border:1.5px solid #555;display:flex;align-items:center;justify-content:center}

/* form */
.field{position:absolute;height:43px;background:#f4f4f4;display:flex;align-items:center;font-size:12.5px;color:#333}
.field .ico{width:42px;height:100%;border-right:1px solid #ddd;display:flex;align-items:center;justify-content:center;margin-right:12px}

/* footer */
.footer-wave{position:absolute;left:0;top:3180px;width:1200px;height:422px}
.foot{position:absolute;color:#fff}
.foot h6{font-size:18px;font-weight:500;letter-spacing:.5px}
.foot h6::after{content:"";display:block;width:22px;height:2px;background:#fff;margin-top:8px}
.foot a{position:absolute;color:#fff;font-size:13px;text-decoration:none}
.social{position:absolute;top:3478px;width:22px;height:22px;border-radius:50%}
.copyright{position:absolute;top:3550px;left:0;width:1200px;height:52px;background:var(--teal-dark);color:#fff;font-size:13px;display:flex;align-items:center;justify-content:center}
</style>
</head>
<body>

<header class="hero">
  <div class="hero-photo" role="img" aria-label="Misty mountain range beneath a soft sunrise sky"></div>
  <svg class="abs" style="left:0;top:500px" width="1200" height="120" viewBox="0 0 1200 120" aria-hidden="true">
    <path d="M0 18 C200 110 420 115 620 60 C820 5 1050 20 1200 110 L1200 120 L0 120Z" fill="var(--mint)"/>
    <path d="M0 18 C200 110 420 115 620 60 C820 5 1050 20 1200 110" fill="none" stroke="var(--blue)" stroke-width="6"/>
  </svg>
  <div class="hero-logo" aria-hidden="true"></div>
  <h1 class="abs center hero-title">Wellness, Meaning, and the Inner Journey</h1>
  <h2 class="abs center hero-sub">The Research Program</h2>
  <p class="abs center hero-text">Lorem Ipsum Dolor Sit Amet, Consectetur Adipiscing Elit,<br>Sed Do Eiusmod Tempor Incididunt Ut Labore</p>
  <a class="btn" style="left:525px;top:415px">Contact Us</a>
</header>

<nav class="topnav">
  <div class="nav-item active" style="left:263px"><svg viewBox="0 0 20 20" fill="none" stroke="currentColor" stroke-width="1.6"><path d="M3 9l7-6 7 6v8H3z"/><path d="M8 17v-5h4v5"/></svg>Home</div>
  <div class="nav-item" style="left:389px"><svg viewBox="0 0 20 20" fill="none" stroke="currentColor" stroke-width="1.6"><circle cx="7" cy="7" r="3"/><circle cx="14" cy="7" r="2.5"/><path d="M1 17c0-4 3-6 6-6s6 2 6 6M13 11c3 0 6 2 6 5"/></svg>People</div>
  <div class="nav-item" style="left:515px"><svg viewBox="0 0 20 20" fill="none" stroke="currentColor" stroke-width="1.6"><rect x="3" y="4" width="12" height="13" rx="1"/><path d="M9 12l8-8"/></svg>Projects</div>
  <div class="nav-item" style="left:641px"><svg viewBox="0 0 20 20" fill="none" stroke="currentColor" stroke-width="1.6"><circle cx="10" cy="10" r="7"/><circle cx="10" cy="10" r="3"/></svg>Resources</div>
  <div class="nav-item" style="left:766px"><svg viewBox="0 0 20 20" fill="none" stroke="currentColor" stroke-width="1.6"><circle cx="10" cy="10" r="7"/><path d="M8 8a2 2 0 1 1 2 2v2M10 14v.5"/></svg>FAQs</div>
  <div class="nav-item" style="left:891px"><svg viewBox="0 0 20 20" fill="none" stroke="currentColor" stroke-width="1.6"><path d="M4 3l3 1 1 4-2 1a9 9 0 0 0 5 5l1-2 4 1 1 3c-8 1-14-5-13-13z"/></svg>Contact Us</div>
</nav>

<!-- Vision -->
<section class="band-mint" style="top:608px;height:791px"></section>
<h2 class="abs center sec-title" style="top:660px">Our <span>Vision</span></h2>
<svg class="abs" style="left:570px;top:706px" width="60" height="12" aria-hidden="true"><path d="M0 6h22M38 6h22" stroke="var(--green)"/><circle cx="30" cy="6" r="4" fill="none" stroke="var(--green)"/></svg>
<p class="abs center lead" style="top:736px">Lorem ipsum dolor sit amet, consectetur adipiscing elit, sed do eiusmod tempor incididunt ut labore et dolore<br>magna aliqua. Ut enim ad minim veniam,  quis nostrud exercitation ullamco laboris. Lorem ipsum dolor sit amet,<br>magna aliqua. Ut enim ad minim veniam,  quis nostrud exercitation ullamco laboris</p>

<article class="v-card" style="left:161px">
  <div class="v-photo" role="img" aria-label="Colleagues working together at a laptop" style="background:linear-gradient(135deg,#6d5a4a,#c9b8a3 60%,#8c7a68)"></div>
  <div class="v-icon"><svg width="34" height="30" viewBox="0 0 34 30" fill="none" stroke="#fff" stroke-width="1.6"><circle cx="17" cy="9" r="5"/><circle cx="7" cy="12" r="3.5"/><circle cx="27" cy="12" r="3.5"/><path d="M8 28c0-6 4-9 9-9s9 3 9 9M1 27c0-4 2-7 6-7M33 27c0-4-2-7-6-7"/></svg></div>
  <h3>PEOPLE</h3>
  <p>Lorem Ipsum Dolor Sit Amet, Consectetur Adipiscing Elit, Sed Do Labore Et Dolore Magna</p>
</article>
<article class="v-card" style="left:464px">
  <div class="v-photo" role="img" aria-label="Researchers in a laboratory using a microscope" style="background:linear-gradient(135deg,#b7c3cc,#e9eef2 55%,#9eafbc)"></div>
  <div class="v-icon"><svg width="30" height="32" viewBox="0 0 30 32" fill="none" stroke="#fff" stroke-width="1.6"><rect x="4" y="5" width="20" height="25" rx="2"/><path d="M10 5V2h8v3M8 13h8M8 19h8M8 25h6M20 12l3 3 6-7"/></svg></div>
  <h3>PROJECTS</h3>
  <p>Lorem Ipsum Dolor Sit Amet, Consectetur Adipiscing Elit, Sed Do Labore Et Dolore Magna</p>
</article>
<article class="v-card" style="left:765px">
  <div class="v-photo" role="img" aria-label="Thoughtful man in front of a chalkboard of question marks" style="background:linear-gradient(135deg,#2f2f2f,#555 60%,#3a3a3a)"></div>
  <div class="v-icon"><svg width="32" height="30" viewBox="0 0 32 30" fill="none" stroke="#fff" stroke-width="1.6"><rect x="2" y="10" width="18" height="13" rx="2"/><path d="M6 23v5l5-5M6 15h10M6 19h7"/><circle cx="23" cy="9" r="7"/><path d="M21 7a2 2 0 1 1 2 2v2"/></svg></div>
  <h3>FAQ'S</h3>
  <p>Lorem Ipsum Dolor Sit Amet, Consectetur Adipiscing Elit, Sed Do Labore Et Dolore Magna</p>
</article>
<a class="btn" style="left:530px;top:1280px">Read More</a>

<!-- Pillars -->
<h2 class="abs center sec-title" style="top:1462px">Our <span>Three Pillars</span></h2>
<svg class="abs" style="left:570px;top:1508px" width="60" height="12" aria-hidden="true"><path d="M0 6h22M38 6h22" stroke="var(--green)"/><circle cx="30" cy="6" r="4" fill="none" stroke="var(--green)"/></svg>
<p class="abs center lead" style="top:1545px">Lorem Ipsum Dolor Sit Amet, Consectetur Adipiscing Elit, Sed Do Eiusmod<br>Tempor Incididunt Ut Labore Et Dolore.</p>

<div class="abs center pillar" style="top:1610px">
  <h4>Values</h4>
  <p>Lorem Ipsum Dolor Sit Amet, Consectetur Adipiscing Elit, Sed<br>Do Eiusmod Tempor Incididunt Ut Labore Et Dolore Magna</p>
  <span class="more">Know More</span>
</div>
<div class="abs pillar" style="top:1836px;left:150px;width:284px;text-align:right">
  <h4>Health care</h4>
  <p>Lorem Ipsum Dolor Sit Amet, Consectetur Adipiscing Elit, Sed Do Eiusmod Tempor Incididunt Ut Labore Et Dolore Magna</p>
  <span class="more">Know More</span>
</div>
<div class="abs pillar" style="top:1838px;left:766px;width:260px">
  <h4>Spiritual Life</h4>
  <p>Lorem Ipsum Dolor Sit Amet, Consectetur Adipiscing Elit, Sed Do Eiusmod Tempor Incididunt Ut Labore Et Dolore Magna</p>
  <span class="more">Know More</span>
</div>

<svg class="abs" style="left:450px;top:1715px" width="300" height="270" viewBox="450 1715 300 270" aria-label="Three overlapping circles: values, health care and spiritual life">
  <circle cx="600" cy="1804" r="82" fill="#1471bd"/>
  <circle cx="543" cy="1895" r="82" fill="#16b49a" fill-opacity=".95"/>
  <circle cx="657" cy="1895" r="82" fill="#6fd6c6" fill-opacity=".9"/>
  <circle cx="599" cy="1860" r="38" fill="#fff"/>
  <circle cx="599" cy="1860" r="20" fill="var(--green)"/>
  <g fill="none" stroke="#fff" stroke-width="2">
    <path d="M580 1770h22l8 10-19 22-19-22z"/><circle cx="612" cy="1762" r="8"/>
    <path d="M518 1912c-14-11-22-18-22-28a10 10 0 0 1 20-3 10 10 0 0 1 20 3c0 4-1 7-4 10"/><path d="M500 1896h8l4-6 5 12 4-6h6"/><circle cx="538" cy="1905" r="7"/><path d="M538 1901v8M534 1905h8"/>
    <path d="M680 1922l-20-34-20 34z"/><circle cx="660" cy="1908" r="6"/><path d="M650 1908c6-7 14-7 20 0-6 7-14 7-20 0"/>
  </g>
</svg>

<!-- Projects -->
<section class="band-mint" style="top:2053px;height:586px"></section>
<h2 class="abs center sec-title" style="top:2120px">Our <span>Projects</span></h2>
<svg class="abs" style="left:570px;top:2166px" width="60" height="12" aria-hidden="true"><path d="M0 6h22M38 6h22" stroke="var(--green)"/><circle cx="30" cy="6" r="4" fill="none" stroke="var(--green)"/></svg>
<p class="abs center lead" style="top:2195px">Lorem Ipsum Dolor Sit Amet, Consectetur Adipiscing Elit, Sed Do</p>

<div class="arrow" style="left:84px"><svg width="12" height="12" viewBox="0 0 12 12"><path d="M8 1L3 6l5 5" fill="none" stroke="#333" stroke-width="1.8"/></svg></div>
<div class="arrow" style="left:1076px"><svg width="12" height="12" viewBox="0 0 12 12"><path d="M4 1l5 5-5 5" fill="none" stroke="#333" stroke-width="1.8"/></svg></div>

<article class="p-card" style="left:161px">
  <div class="p-photo" role="img" aria-label="Scientists examining samples in a lab" style="background:linear-gradient(180deg,#2b6cb5,#5f8fc4 45%,#2d3f55)"></div>
  <h5 style="top:192px">Project 1</h5><small style="top:218px">Lorem Ipsum Dolor Sit Amet</small>
  <div class="plus" style="top:246px">+</div>
</article>
<article class="p-card" style="left:387px;border:3px solid #555">
  <div class="p-photo" role="img" aria-label="Researcher in a laboratory under a green overlay" style="background:linear-gradient(180deg,#64a63f,#7fb557 60%,#8aa45a);border-radius:6px"></div>
  <h5 style="top:122px">Project 2</h5><small style="top:148px">Lorem Ipsum Dolor Sit Amet</small>
  <div class="plus" style="top:183px;left:82px">+</div>
</article>
<article class="p-card" style="left:613px">
  <div class="p-photo" role="img" aria-label="Two colleagues talking in an office" style="background:linear-gradient(180deg,#6b6f74,#4a4d52 50%,#24272b)"></div>
  <h5 style="top:192px">Project 3</h5><small style="top:218px">Lorem Ipsum Dolor Sit Amet</small>
  <div class="plus" style="top:246px">+</div>
</article>
<article class="p-card" style="left:838px">
  <div class="p-photo" role="img" aria-label="Team members reviewing work together" style="background:linear-gradient(180deg,#b9bec3,#6b7480 55%,#273a5a)"></div>
  <h5 style="top:192px">Project 4</h5><small style="top:218px">Lorem Ipsum Dolor Sit Amet</small>
  <div class="plus" style="top:246px">+</div>
</article>

<!-- Contact form -->
<h2 class="abs center sec-title" style="top:2700px">Our <span>Projects</span></h2>
<svg class="abs" style="left:570px;top:2746px" width="60" height="12" aria-hidden="true"><path d="M0 6h22M38 6h22" stroke="var(--green)"/><circle cx="30" cy="6" r="4" fill="none" stroke="var(--green)"/></svg>
<p class="abs center lead" style="top:2772px">Lorem Ipsum Dolor Sit Amet, Consectetur Adipiscing Elit, Sed Do</p>

<div class="field" style="left:241px;top:2834px;width:342px"><span class="ico"><svg width="12" height="12" viewBox="0 0 12 12" fill="#aaa"><circle cx="6" cy="3.5" r="3"/><path d="M0 12c0-4 3-5 6-5s6 1 6 5z"/></svg></span>Your Name*</div>
<div class="field" style="left:610px;top:2834px;width:342px"><span class="ico"><svg width="10" height="13" viewBox="0 0 10 13" fill="#aaa"><path d="M5 0a5 5 0 0 1 5 5c0 3-5 8-5 8S0 8 0 5a5 5 0 0 1 5-5z"/><circle cx="5" cy="5" r="2" fill="#f4f4f4"/></svg></span>Email*</div>
<div class="field" style="left:241px;top:2892px;width:342px"><span class="ico"><svg width="12" height="12" viewBox="0 0 12 12" fill="#aaa"><path d="M1 1l3 0 1 3-2 1a7 7 0 0 0 4 4l1-2 3 1v3C5 11 1 7 1 1z"/></svg></span>Phone*</div>
<div class="field" style="left:610px;top:2892px;width:342px"><span class="ico"><svg width="13" height="12" viewBox="0 0 13 12" fill="none" stroke="#aaa" stroke-width="1.3"><rect x="1" y="2" width="9" height="9"/><path d="M5 8l7-7"/></svg></span>Inquiry For*</div>
<div class="field" style="left:241px;top:2954px;width:709px;height:109px;align-items:flex-start"><span class="ico" style="height:43px"><svg width="13" height="13" viewBox="0 0 13 13" fill="none" stroke="#aaa" stroke-width="1.2"><circle cx="6.5" cy="6.5" r="5.5"/><path d="M5 5a1.5 1.5 0 1 1 1.5 1.5V8M6.5 9.5v.5"/></svg></span><span style="margin-top:14px">How can we help you?</span></div>
<a class="btn" style="left:530px;top:3113px;background:var(--blue-dark)">Submit Now</a>

<!-- Footer -->
<svg class="footer-wave" viewBox="0 0 1200 422" preserveAspectRatio="none" aria-hidden="true">
  <path d="M0 12 C180 80 380 100 620 60 C850 20 1030 0 1200 40 L1200 422 L0 422Z" fill="var(--teal)"/>
  <path d="M0 12 C180 80 380 100 620 60 C850 20 1030 0 1200 40" fill="none" stroke="var(--blue)" stroke-width="5"/>
</svg>

<div class="foot" style="left:161px;top:3330px;display:flex;align-items:center">
  <span style="width:40px;height:40px;border-radius:50%;border:2px solid #fff;margin-right:10px"></span>
  <span style="font-size:12px;font-weight:600;line-height:15px;border-left:1px solid #fff;padding-left:8px">Wellness, Meaning, and the Inner Journey<br>The Research Program</span>
</div>
<p class="foot" style="left:161px;top:3392px;width:310px;font-size:11.5px;line-height:19.5px">Lorem Ipsum Dolor Sit Amet, Consectetur Adipiscing Elit, Sed Do Eiusmod Tempor Incididunt Ut Labore Et Dolore Magna</p>
<span class="social" style="left:161px;background:#2f5aa8" role="img" aria-label="Social link"></span>
<span class="social" style="left:199px;background:#2aa4e0" role="img" aria-label="Social link"></span>
<span class="social" style="left:237px;background:#1a6fb0" role="img" aria-label="Social link"></span>
<span class="social" style="left:274px;background:#d94a35" role="img" aria-label="Social link"></span>

<div class="foot" style="left:547px;top:3322px"><h6>QUICK LINKS</h6></div>
<div class="foot" style="left:0;top:0">
  <a style="left:548px;top:3366px">Home</a>
  <a style="left:548px;top:3403px">Our Vision</a>
  <a style="left:548px;top:3441px">People</a>
  <a style="left:548px;top:3481px">Projects</a>
  <a style="left:651px;top:3366px">Resources</a>
  <a style="left:652px;top:3403px">FAQs</a>
  <a style="left:653px;top:3441px">Contact Us</a>
</div>

<div class="foot" style="left:810px;top:3322px"><h6>CONTACT DETAILS</h6></div>
<div class="foot" style="left:810px;top:3366px;font-size:13px;line-height:21px;display:flex">
  <svg width="10" height="14" viewBox="0 0 10 13" fill="#fff" style="margin:3px 16px 0 0"><path d="M5 0a5 5 0 0 1 5 5c0 3-5 8-5 8S0 8 0 5a5 5 0 0 1 5-5z"/><circle cx="5" cy="5" r="2" fill="var(--teal)"/></svg>
  <span>48, Alder Lane, Brookfield,<br>Westmoor</span>
</div>
<div class="foot" style="left:810px;top:3430px;font-size:13px;display:flex;align-items:center">
  <svg width="13" height="13" viewBox="0 0 12 12" fill="#fff" style="margin-right:14px"><path d="M1 1l3 0 1 3-2 1a7 7 0 0 0 4 4l1-2 3 1v3C5 11 1 7 1 1z"/></svg>555-014-2290
</div>
<div class="foot" style="left:810px;top:3482px;font-size:13px;display:flex;align-items:center">
  <svg width="14" height="10" viewBox="0 0 14 10" fill="none" stroke="#fff" stroke-width="1.3" style="margin-right:13px"><rect x=".5" y=".5" width="13" height="9"/><path d="M.5 .5L7 6l6.5-5.5"/></svg>hello@wmijresearch.org
</div>

<div class="copyright">Copyright © 2021 WMIJ Research Program. All Rights Reserved.</div>

</body>
</html>
```